Brookvane Consulting Business Card Design

Business Card Design for Brookvane Consulting. Brookvane Consulting is a boutique consultancy based in Atlanta, GA., that specializes in marketing strategy, organization planning, and leadership development. We provide solutions for small businesses and startups as well as Vantage 300 companies.

http://brookvaneconsulting.com/

Target Market(s)

We provide solutions for small businesses and startups as well as Vantage 300 companies.

Industry/Entity Type

Consulting

Contact Information for Business Card

Two sided business card with priority on contact information, logo, tag line (Guidance to Plan Wisely, Act Boldly, Grow Further)

Colors

Designer to choose colors to be used in the design.

Requirements
Must have
• contact information, logo, tag line (Guidance to Plan Wisely, Act Boldly, Grow Further)
• Simple no over communication.
Nice to have
• I would like to see different placements of logo and creative use of both sides of the card
Should not have
• Do not put too much information on the card.

```html
<!DOCTYPE html>
<html lang="en">
<head>
<meta charset="utf-8">
<title>Brookvane Consulting Business Card</title>
<link rel="stylesheet" href="https://fonts.googleapis.com/css2?family=Roboto:wght@400;500&family=Roboto+Condensed:wght@700&display=swap">
<style>
  :root {
    --stage: #2b2b2c;
    --card-front: #1c1c1d;
    --card-back: #262627;
    --white: #ffffff;
    --text-light: #e6e6e6;
    --name-grey: #a9a9a9;
    --band-grey: #a6a6a6;
    --divider: #cfcfcf;
  }
  * { margin: 0; padding: 0; box-sizing: border-box; }
  html, body {
    width: 1200px; height: 960px; overflow: hidden;
    background: var(--stage);
    font-family: "Roboto", Arial, sans-serif;
  }
  .canvas { position: relative; width: 1200px; height: 960px; }

  .card { position: absolute; width: 600px; height: 343px; overflow: hidden; }

  /* Front */
  .card-front { left: 314px; top: 113px; background: var(--card-front); }
  .brand-name {
    color: var(--white); font-weight: 500; letter-spacing: 0.5px; white-space: nowrap;
  }
  .card-front .brand-name { position: absolute; left: 46px; top: 58px; font-size: 32px; }
  .name-marker { position: absolute; left: 0; top: 232px; width: 15px; height: 38px; background: var(--white); }
  .holder-name {
    position: absolute; left: 46px; top: 229px;
    font-family: "Roboto Condensed", Arial, sans-serif; font-weight: 700;
    font-size: 21px; color: var(--name-grey); letter-spacing: 0.2px; white-space: nowrap;
  }
  .holder-title {
    position: absolute; left: 46px; top: 254px;
    font-size: 16px; font-weight: 500; color: var(--text-light); white-space: nowrap;
  }
  .divider { position: absolute; left: 298px; top: 222px; width: 1px; height: 61px; background: var(--divider); }
  .contact-list { position: absolute; left: 315px; top: 224px; list-style: none; }
  .contact-list li {
    display: flex; align-items: center; gap: 8px;
    height: 19.5px; font-size: 14.5px; color: var(--text-light); white-space: nowrap;
  }
  .contact-list svg { width: 14px; height: 14px; fill: var(--name-grey); flex: none; }
  .edge-bands { position: absolute; left: 0; top: 331px; width: 600px; height: 12px; }

  /* Back */
  .card-back { left: 311px; top: 472px; }
  .back-pattern { position: absolute; inset: 0; background: var(--card-back); }
  .card-back .brand-name {
    position: absolute; left: 0; right: 0; top: 120px; text-align: center; font-size: 44px;
  }
  .tagline {
    position: absolute; left: 0; right: 0; top: 281px; text-align: center;
    font-size: 14.5px; color: var(--text-light); white-space: nowrap;
  }
</style>
</head>
<body>
<main class="canvas">
  <section class="card card-front" aria-label="Card front">
    <div class="brand-name">Brookvane Consulting</div>
    <div class="name-marker"></div>
    <div class="holder-name">DARIUS WHITFIELD</div>
    <div class="holder-title">Founder/Managing Director</div>
    <div class="divider"></div>
    <ul class="contact-list">
      <li>
        <svg viewBox="0 0 16 16" aria-hidden="true"><path d="M3.6 1.2l2.3 2.6-1.3 1.8c.9 2 2.4 3.5 4.4 4.4l1.8-1.3 2.6 2.3-1.1 2.6C7 13.5 2.5 9 2.3 2.3z"/></svg>
        555-013-4827
      </li>
      <li>
        <svg viewBox="0 0 16 16" aria-hidden="true"><path d="M1 3h14v1.2L8 8.6 1 4.2z M1 5.6l7 4.4 7-4.4V13H1z"/></svg>
        darius@brookvaneconsulting.com
      </li>
      <li>
        <svg viewBox="0 0 16 16" aria-hidden="true"><circle cx="8" cy="8" r="6.5"/><path d="M5 4.5l2 1-1 2 2 1.5-1 3M10 4l1 2 2 .5" stroke="#1c1c1d" stroke-width="1.3" fill="none"/></svg>
        brookvaneconsulting.com
      </li>
    </ul>
    <svg class="edge-bands" viewBox="0 0 600 12" aria-hidden="true">
      <polygon points="0,0 361,0 357,12 0,12" fill="var(--band-grey)"/>
      <polygon points="367,0 600,0 600,12 363,12" fill="var(--white)"/>
    </svg>
  </section>

  <section class="card card-back" aria-label="Card back">
    <div class="back-pattern" role="img" aria-label="Repeating dark geometric chevron pattern"></div>
    <div class="brand-name">Brookvane Consulting</div>
    <p class="tagline">Guidance to Plan Wisely, Act Boldly, Grow Further</p>
  </section>
</main>
</body>
</html>
```